Business Cards for IT Consulting Company (Managed Service Provider)

I am looking to have some business cards printed and would like some designs. We are an IT Consulting company based in Vancouver BC. I would like a nice clean and modern look to the cards. I have uploaded all the versions of my logo so parts can be used as needed. Here is a snippit from our website homepage:

Quillbrook Networks Ltd. is an IT Solutions Partner located in Vancouver BC, Canada. We offer IT solutions and support to customers in the greater Vancouver Area. With expertise in Microsoft platforms, as well as Linux and Mac OSX and over 12 years experience in the IT industry, Quillbrook Networks is dedicated to offering our clients top quality service and products. We take pride in the solutions we offer our customers. The greatest compliment a client can give us is to recommend our services.

Quillbrook Networks Ltd. offers a wide range of IT services from onsite service to remote support and managed service solutions. This allows clients to choose the support path that best suits their company’s needs. Supporting many different sized companies from small to enterprise level over the past 12 years Quillbrook Networks has the experience and expertise needed to ensure things run smoothly. Allowing our clients to focus on doing business.

Revolutionizing the way IT services are delivered.

Quillbrook Networks is dedicated to providing our clients with IT solutions that work and grow with them for years to come. This philosophy helps save money in the long run instead of replacing equipment constantly. Far too often IT solutions are not well thought out and while possibly solving the problem at hand, require replacement due to growth or quality within a very short time frame. Quillbrook Networks takes pride in providing solutions that will last and be able to accommodate growth without the need for replacement.

Industry/Entity Type

Information Technology

Contact Information for Business Card

Quillbrook Networks Ltd.
(Employee Name)
Eml: (Employees Email Address)
Web: quillbrook.me
Ph: 604-555-0148

Font styles to use
Serif
Sans Serif

Requirements
Must have
• The Company logo and company colors.
Nice to have
• - Our tag line: "Reimagining Managed IT" or "Revolutionizing the way IT services are delivered."
• - Also I really like the idea of nature and technology together blending which is sort of where my logo came from so integrating that somehow onto the business cards would be great.

```html
<!DOCTYPE html>
<html lang="en">
<head>
<meta charset="utf-8">
<title>Quillbrook Networks Ltd. – Business Cards</title>
<link rel="stylesheet" href="https://fonts.googleapis.com/css2?family=Source+Sans+3:wght@400;600;700&display=swap">
<style>
  :root {
    --backdrop: #4a433f;
    --card: #141414;
    --card-edge: #1c1c1c;
    --brand-blue: #1e9bd7;
    --text-light: #e8e8e8;
    --text-soft: #c9c9c9;
    --divider: #8a8a8a;
    --logo-silver: #d6d6d6;
  }
  * { box-sizing: border-box; margin: 0; padding: 0; }
  html, body { width: 1200px; height: 814px; overflow: hidden; }
  body {
    background: var(--backdrop);
    font-family: "Source Sans 3", Arial, sans-serif;
    display: flex;
    align-items: center;
    justify-content: center;
    gap: 50px;
  }
  .card {
    width: 540px;
    height: 309px;
    background: var(--card);
    border: 1px solid var(--card-edge);
    position: relative;
    box-shadow: 0 10px 30px rgba(0,0,0,0.35);
  }

  /* Front card */
  .front .brand {
    position: absolute;
    top: 70px;
    left: 0;
    right: 0;
    display: flex;
    align-items: center;
    justify-content: center;
    gap: 12px;
  }
  .brand-square {
    width: 22px;
    height: 22px;
    background: var(--brand-blue);
  }
  .front .brand-name {
    color: var(--brand-blue);
    font-weight: 700;
    font-size: 30px;
    letter-spacing: 0.2px;
  }
  .front .details {
    position: absolute;
    top: 158px;
    left: 0;
    right: 0;
    display: flex;
    justify-content: center;
  }
  .person {
    text-align: right;
    padding-right: 22px;
    padding-top: 28px;
  }
  .person-name {
    color: var(--brand-blue);
    font-weight: 600;
    font-size: 24px;
    line-height: 1.1;
    margin-bottom: 4px;
  }
  .person-address {
    color: var(--text-soft);
    font-size: 16px;
    line-height: 1.35;
  }
  .divider {
    width: 1px;
    height: 118px;
    background: var(--divider);
  }
  .contact {
    list-style: none;
    padding-left: 18px;
  }
  .contact li {
    display: flex;
    align-items: center;
    gap: 9px;
    color: var(--text-light);
    font-size: 15.5px;
    line-height: 1;
    margin-bottom: 9px;
  }
  .contact svg { width: 13px; height: 13px; flex: none; }

  /* Back card */
  .back {
    display: flex;
    flex-direction: column;
    align-items: center;
    justify-content: center;
    gap: 34px;
  }
  .back .brand {
    display: flex;
    align-items: center;
    gap: 12px;
  }
  .back .brand-square { background: var(--logo-silver); }
  .back .brand-name {
    color: var(--logo-silver);
    font-weight: 700;
    font-size: 30px;
  }
  .tagline {
    color: var(--text-light);
    font-size: 13px;
    font-weight: 600;
    letter-spacing: 0.2px;
  }
</style>
</head>
<body>

  <section class="card front" aria-label="Business card front">
    <div class="brand">
      <span class="brand-square"></span>
      <span class="brand-name">Quillbrook Networks Ltd.</span>
    </div>
    <div class="details">
      <div class="person">
        <p class="person-name">Dana Whitfield</p>
        <p class="person-address">1420 Cedarline Road<br>Vancouver, BC V5K 0A1</p>
      </div>
      <div class="divider"></div>
      <ul class="contact">
        <li>
          <svg viewBox="0 0 16 16" aria-hidden="true"><path fill="#1e9bd7" d="M3.6 1.2l2.3 2.8-1.3 1.6c.9 2 2.6 3.7 4.7 4.7l1.6-1.3 2.8 2.3-1.2 2.3C6.8 13.4 2.6 9.2 1.4 3.5z"/></svg>
          604-555-0148
        </li>
        <li>
          <svg viewBox="0 0 16 16" aria-hidden="true"><rect x="1" y="3" width="14" height="10" fill="#1e9bd7"/><path d="M1.5 3.5L8 9l6.5-5.5" fill="none" stroke="#141414" stroke-width="1.4"/></svg>
          name@quillbrook.me
        </li>
        <li>
          <svg viewBox="0 0 16 16" aria-hidden="true"><circle cx="8" cy="8" r="7" fill="#1e9bd7"/><path d="M1 8h14M8 1c-3 3-3 11 0 14M8 1c3 3 3 11 0 14" fill="none" stroke="#141414" stroke-width="1.1"/></svg>
          www.quillbrook.me
        </li>
      </ul>
    </div>
  </section>

  <section class="card back" aria-label="Business card back">
    <div class="brand">
      <span class="brand-square"></span>
      <span class="brand-name">Quillbrook Networks Ltd.</span>
    </div>
    <p class="tagline">Reimagining Managed IT</p>
  </section>

</body>
</html>
```